Marlowby Services Website Design

We have most content but require a professional design. We have a logo already and will need it utilized along with several of the photos from the attached documentation.
First page should have our mission and Vision and the synapsis provided in the word document. Visitors will be prompted to select from one of our 3 divisions from this page.
Each division will have the same list of tabs : About, Services, Safety, Careers and Contact.
Photos on each divisions page should be representative of the divisions offerings. The word doc attached contains the requested content and we are open to edits that would complement and fill the website.
I like the Quorvane site www.quorvane.example - they are our competition so cant be modeled directly after this.
Please include prompts to request quote at each service page. align the format of the geotechnical page to the other 2 divisions.
I used chat gpt for some of the content so will need it optimized for SCO.

```html
<!DOCTYPE html>
<html lang="en">
<head>
<meta charset="utf-8">
<title>Marlowby Services</title>
<link rel="stylesheet" href="https://fonts.googleapis.com/css2?family=Poppins:wght@400;500;600;700&display=swap">
<style>
:root{
  --red:#e31e24;
  --ink:#111111;
  --muted:#555555;
  --soft:#fdeaeb;
  --white:#ffffff;
  --black:#000000;
}
*{margin:0;padding:0;box-sizing:border-box}
html,body{width:1200px;height:2741px;overflow:hidden}
body{font-family:'Poppins',sans-serif;color:var(--ink);background:var(--white);position:relative}
.abs{position:absolute}
a{color:inherit;text-decoration:none}

.site-header{position:absolute;left:0;top:0;width:1200px;height:71px;background:var(--white)}
.brand{position:absolute;left:141px;top:17px;font-weight:700;font-size:30px;letter-spacing:2px;color:var(--red);line-height:36px}
.main-nav{position:absolute;top:27px;font-size:13px;font-weight:500}
.btn{position:absolute;display:flex;align-items:center;justify-content:center;font-size:13px;font-weight:600;border-radius:5px}
.btn-red{background:var(--red);color:var(--white)}
.btn-white{background:var(--white);color:var(--red)}

.hero{position:absolute;left:0;top:71px;width:1200px;height:458px;background:linear-gradient(180deg,#3a3f36 0%,#4b4c42 45%,#3b3a35 100%)}
.hero-sub{position:absolute;top:221px;width:1200px;text-align:center;color:var(--white);font-size:15px}
.hero-title{position:absolute;top:252px;width:1200px;text-align:center;color:var(--white);font-size:36px;font-weight:600;line-height:56px}

.section-title{position:absolute;width:1200px;text-align:center;font-size:28px;font-weight:600}
.rule{position:absolute;height:2px;width:75px;background:var(--red)}

.division{position:absolute;top:704px;width:292px;height:212px;border-radius:12px;overflow:hidden}
.division-label{position:absolute;left:0;width:100%;text-align:center;color:var(--white);font-size:17px;font-weight:600;line-height:24px}
.division-go{position:absolute;right:14px;bottom:12px;width:32px;height:32px;border-radius:50%;background:var(--white)}

.svc-title{position:absolute;font-size:15px;font-weight:500}
.svc-text{position:absolute;font-size:12px;color:var(--muted);line-height:20.5px;width:210px}
.icon-ring{position:absolute;border-radius:50%;background:var(--soft)}

.vision-photo{position:absolute;left:0;top:1517px;width:511px;height:387px;background:linear-gradient(160deg,#4d5a45 0%,#8a8a80 55%,#a09b90 100%)}
.vision-card{position:absolute;left:457px;top:1545px;width:602px;height:421px;background:var(--white);box-shadow:0 4px 30px rgba(0,0,0,.08)}
.block-title{position:absolute;font-size:26px;font-weight:600}
.block-text{position:absolute;left:489px;width:562px;font-size:13px;color:#333;line-height:22.6px}

.cta{position:absolute;left:141px;top:2068px;width:918px;height:214px;background:var(--soft);border-radius:20px}
.cta-text{position:absolute;top:2109px;width:1200px;text-align:center;font-size:16.5px;font-weight:500;line-height:25px}

.site-footer{position:absolute;left:0;top:2393px;width:1200px;height:348px;background:var(--black);color:var(--white)}
.foot-head{position:absolute;top:55px;font-size:16px;font-weight:500}
.foot-list{position:absolute;list-style:none;font-size:13px;line-height:29.2px;top:96px}
.foot-item{position:absolute;font-size:13px;line-height:19px}
.social{position:absolute;top:2700px;width:24px;height:24px;border-radius:50%;background:var(--white);border:5px solid var(--red)}
</style>
</head>
<body>

<header class="site-header">
  <div class="brand">MARLOWBY</div>
  <nav>
    <a class="main-nav" style="left:648px">About Us</a>
    <a class="main-nav" style="left:730px">Services</a>
    <a class="main-nav" style="left:808px">Safety</a>
    <a class="main-nav" style="left:873px">Careers</a>
  </nav>
  <a class="btn btn-red" style="left:950px;top:18px;width:109px;height:34px">Contact Us</a>
</header>

<section class="hero" role="img" aria-label="Aerial view of a small town with a lift truck beside a tall tower"></section>
<p class="hero-sub">Delivering safe, reliable access and maintenance services to</p>
<h1 class="hero-title">Oil &amp; Gas, Construction, Utility &amp;<br>Renewable energy Sector</h1>
<a class="btn btn-white" style="left:546px;top:385px;width:108px;height:35px">Contact Us</a>

<h2 class="section-title" style="top:615px">Our Divisions</h2>
<div class="rule" style="left:562px;top:660px"></div>

<a class="division" style="left:141px;background:linear-gradient(180deg,#5d86b8 0%,#8fb0cf 60%,#6c6a55 100%)" role="img" aria-label="Aerial lift working on a water tower">
  <span class="division-label" style="top:94px">Aerial Access</span><span class="division-go"></span>
</a>
<a class="division" style="left:454px;background:linear-gradient(180deg,#2d4a2a 0%,#4d6a3a 50%,#6a2a2a 100%)" role="img" aria-label="Red tracked geotechnical drilling rig">
  <span class="division-label" style="top:94px">Geotechnical Drilling</span><span class="division-go"></span>
</a>
<a class="division" style="left:767px;background:linear-gradient(160deg,#1f4e9a 0%,#2f62b0 60%,#9aaac4 100%)" role="img" aria-label="Wind turbine tower seen from below">
  <span class="division-label" style="top:82px">Renewable Energy<br>Services</span><span class="division-go"></span>
</a>
<svg class="abs" style="left:0;top:0" width="1200" height="1000" aria-hidden="true">
  <g stroke="#111" stroke-width="1.8" fill="none" stroke-linecap="round">
    <path d="M396 895 L409 882 M400 882 H409 V891"/>
    <path d="M709 895 L722 882 M713 882 H722 V891"/>
    <path d="M1022 895 L1035 882 M1026 882 H1035 V891"/>
  </g>
</svg>

<h2 class="section-title" style="top:1002px">Our Services</h2>
<div class="rule" style="left:562px;top:1047px"></div>
<p class="abs" style="top:1066px;width:1200px;text-align:center;font-size:14.5px">Delivering safe, reliable aerial access and maintenance services</p>

<div class="abs" style="left:450px;top:1127px;width:298px;height:298px;border-radius:50%;background:radial-gradient(circle at 50% 50%,#d8d8d4 0%,#9a8666 40%,#6c5a3e 100%)" role="img" aria-label="Overhead view of a white lift truck parked on a field"></div>

<span class="svc-title" style="right:867px;top:1182px">Renewable Energy Industries</span>
<p class="svc-text" style="left:126px;top:1209px;text-align:right">Lorem Ipsum is simply dummy text of the printing and typesetting industry.</p>
<span class="svc-title" style="right:867px;top:1305px">Oil &amp; Gas</span>
<p class="svc-text" style="left:126px;top:1333px;text-align:right">Lorem Ipsum is simply dummy text of the printing and typesetting industry.</p>
<span class="svc-title" style="left:865px;top:1182px">Construction</span>
<p class="svc-text" style="left:865px;top:1209px">Lorem Ipsum is simply dummy text of the printing and typesetting industry.</p>
<span class="svc-title" style="left:865px;top:1305px">Utility</span>
<p class="svc-text" style="left:865px;top:1333px">Lorem Ipsum is simply dummy text of the printing and typesetting industry.</p>

<div class="icon-ring" style="left:351px;top:1176px;width:64px;height:64px"></div>
<div class="icon-ring" style="left:351px;top:1299px;width:64px;height:64px"></div>
<div class="icon-ring" style="left:783px;top:1176px;width:64px;height:64px"></div>
<div class="icon-ring" style="left:783px;top:1299px;width:64px;height:64px"></div>
<svg class="abs" style="left:0;top:1170px" width="1200" height="200" aria-hidden="true">
  <g stroke="#e31e24" stroke-width="1.8" fill="none" stroke-linejoin="round">
    <path d="M368 30 L383 20 L398 30 Z M383 30 V44 M370 50 Q383 36 396 50"/>
    <rect x="370" y="143" width="14" height="26"/><rect x="386" y="152" width="12" height="17"/><path d="M374 150h6M374 157h6M390 159h4"/>
    <path d="M803 20 V52 M796 52 H812 M803 24 H830 M803 24 L815 16 L830 24 M826 24 V36"/><rect x="822" y="36" width="8" height="6"/>
    <path d="M800 165 L815 152 L830 165 V172 H800 Z M817 156 L812 164 H818 L813 171"/><path d="M801 145 V160 M806 143 V160"/>
  </g>
</svg>

<div class="vision-photo" role="img" aria-label="White lift truck with extended boom on a gravel lot"></div>
<div class="vision-card"></div>
<div class="icon-ring" style="left:489px;top:1572px;width:56px;height:56px"></div>
<div class="icon-ring" style="left:489px;top:1747px;width:56px;height:56px"></div>
<svg class="abs" style="left:489px;top:1572px" width="56" height="231" aria-hidden="true">
  <g stroke="#e31e24" stroke-width="1.8" fill="none" stroke-linecap="round">
    <circle cx="28" cy="25" r="8"/><path d="M24 34 H32 M25 38 H31 M28 10 V13 M16 25 H13 M40 25 H43 M19 16 L17 14 M37 16 L39 14"/>
    <circle cx="28" cy="203" r="11"/><circle cx="28" cy="203" r="5"/><path d="M28 203 L42 189 M38 189 H42 V193"/>
  </g>
</svg>
<h2 class="block-title" style="left:564px;top:1581px">Our Vision</h2>
<div class="rule" style="left:564px;top:1620px"></div>
<p class="block-text" style="top:1651px">To be the leading provider of aerialaccess, geotechnical drilling, and service solutions, setting the standard forexcellence in safety, efficiency, and environmental stewardship.</p>
<h2 class="block-title" style="left:564px;top:1755px">Our Mission</h2>
<div class="rule" style="left:564px;top:1795px"></div>
<p class="block-text" style="top:1824px">AtMarlowby, our mission is to deliver unparalleled aerial access, geotechnicaldrilling, and service and maintenance solutions, consistently exceeding ourclients' expectations. We strive to achieve this by investing in cutting-edgetechnology, fostering a culture of safety and continuous improvement, andprioritizing environmental sustainability.</p>

<div class="cta"></div>
<p class="cta-text">Marlowby Is A Full-Service Wind Energy Service Provider Specializing In Blade<br>Access And Repair, Service And Maintenance, And Trouble Shooting On Most<br>Wind Turbine Platforms.</p>
<a class="btn btn-red" style="left:546px;top:2213px;width:108px;height:34px">Contact Us</a>
<div class="abs" style="left:797px;top:2206px;width:274px;height:100px;border-radius:10px;background:linear-gradient(180deg,#f3f3f3 0%,#d6d6d6 60%,#3a3a3a 100%)" role="img" aria-label="White lift truck with folded boom"></div>

<footer class="site-footer">
  <div class="brand" style="top:53px;color:var(--white)">MARLOWBY</div>
  <h3 class="foot-head" style="left:451px">Quick Links</h3>
  <ul class="foot-list" style="left:451px"><li>Home</li><li>About Us</li><li>Services</li><li>Safety</li><li>Careers</li></ul>
  <h3 class="foot-head" style="left:652px">Company</h3>
  <ul class="foot-list" style="left:652px"><li>Terms &amp; Condition</li><li>Privacy Policy</li><li>Contact Us</li></ul>
  <h3 class="foot-head" style="left:849px">Contact Info</h3>
  <svg class="abs" style="left:848px;top:100px" width="20" height="100" aria-hidden="true">
    <g fill="none" stroke="#fff" stroke-width="1.6">
      <path d="M9 18 C3 11 3 4 9 2 C15 4 15 11 9 18 Z"/><circle cx="9" cy="8" r="2.3"/>
    </g>
    <rect x="1" y="50" width="16" height="11" fill="#fff"/><path d="M1 50 L9 56 L17 50" stroke="#000" stroke-width="1.2" fill="none"/>
    <path d="M3 80 C3 88 9 94 16 94 L16 90 L12 88 L10 90 C8 89 6 87 5 85 L7 83 L5 79 Z" fill="#fff"/>
  </svg>
  <p class="foot-item" style="left:878px;top:98px">58 Larchmont Road Fernvale<br>AB T0X-1B0</p>
  <p class="foot-item" style="left:876px;top:147px">info@marlowby.example</p>
  <p class="foot-item" style="left:875px;top:177px">555 010 2486</p>
  <div class="abs" style="left:141px;top:290px;width:918px;height:1px;background:#444"></div>
  <p class="foot-item" style="left:141px;top:310px">© 2024 Marlowby. All Rights Reserved.</p>
</footer>
<span class="social" style="left:926px"></span>
<span class="social" style="left:962px"></span>
<span class="social" style="left:998px"></span>
<span class="social" style="left:1035px"></span>

</body>
</html>
```